Web Design Project for SEARCH ENGINE !

We need a website design for torrents search engine.

The Website will be www.Qentrova.com

Qentrova is a a search engine for torrents.
Qentrova search and index torrents results from all torrents sites.

We will need:
Logo
WebSite Design
slogen (optional)

we need only PSDs - no codded pages are needed !

Design to the following screen Size & resolution: 1024 x 768

***PLEASE DOWNLOAD ATTACHED FILE !

```html
<!DOCTYPE html>
<html lang="en">
<head>
<meta charset="utf-8">
<title>Qentrova – Torrents Search Engine</title>
<link rel="stylesheet" href="https://fonts.googleapis.com/css2?family=Lato:wght@400;700&family=Arimo:wght@400&display=swap">
<style>
:root{
  --bar-dark:#1c1c1c;
  --bar-mid:#3a3a3a;
  --accent-green:#5cb82e;
  --accent-red:#d8201f;
  --accent-orange:#f08a24;
  --badge-blue:#1fa3e0;
  --badge-green:#7cbc3a;
  --text-dark:#2f2f2f;
  --text-mid:#555;
  --text-soft:#8a8a8a;
  --field:#d6d6d6;
  --filter-light:#dadada;
  --filter-dark:#c3c3c3;
  --rule:#9a9a9a;
  --page:#f3f3f3;
}
*{box-sizing:border-box;margin:0;padding:0}
html,body{width:1200px;height:896px;overflow:hidden;background:#fff}
body{font-family:"Lato",sans-serif;color:var(--text-dark)}
.stage{width:1024px;height:768px;position:relative;transform:scale(1.171875,1.1666667);transform-origin:0 0;
  background:linear-gradient(#e9e9e9,#fbfbfb 40%,#f7f7f7 80%,#e6e6e6)}
.abs{position:absolute}
a{color:inherit;text-decoration:none}

.topbar{left:6px;top:3px;width:1012px;height:30px;background:linear-gradient(#3c3c3c,var(--bar-dark));}
.nav{position:absolute;left:0;right:0;top:7px;text-align:center;font-size:13px;color:#fff;letter-spacing:.2px;padding-right:90px}
.nav span.sep{margin:0 6px}
.nav .current{color:var(--accent-green)}
.lang{position:absolute;left:740px;top:6px;width:60px;height:19px;background:var(--accent-green);color:#fff;font-size:11px;padding:3px 0 0 7px}
.lang svg{position:absolute;right:6px;top:6px}

.brand{left:16px;top:54px;width:145px}
.brand-row{display:flex;align-items:center;gap:4px}
.brand-mark{width:23px;height:23px;background:var(--accent-green)}
.brand-name{font-size:25px;font-weight:700;color:#4a4a4a;line-height:25px;letter-spacing:-.5px}
.brand-tag{font-size:10.5px;color:#555;letter-spacing:.1px;margin-top:1px}

.search-field{left:166px;top:53px;width:636px;height:27px;background:var(--field);font-family:"Arimo",sans-serif;font-size:16px;padding:5px 8px;color:#333}
.search-btn{left:802px;top:53px;width:56px;height:27px;background:#111;color:#fff;font-size:8.5px;display:flex;align-items:center;justify-content:center;gap:3px}
.result-stats{left:166px;top:85px;font-size:9.5px;color:#444}
.site-include{left:764px;top:85px;font-size:9.5px;color:#444;display:flex;align-items:center;gap:4px}
.site-include i{display:inline-block;width:10px;height:10px;border:1px solid #777;background:#eee}

.filter-top{left:166px;top:113px;width:692px;height:19px;background:var(--filter-light);font-size:9.5px;color:#444}
.filter-top .count{position:absolute;left:6px;top:4px}
.filter-top .order{position:absolute;right:6px;top:4px}
.red{color:var(--accent-red)}
.pager-tab{left:430px;top:109px;width:166px;height:19px;background:#1e1e1e;border-radius:4px 4px 0 0;color:#fff;font-size:9.5px;text-align:center;padding-top:3px}
.pager-tab .on{color:var(--accent-green)}
.filter-bottom{left:166px;top:133px;width:692px;height:19px;background:var(--filter-dark);font-size:9.5px;color:#444;text-align:center;padding-top:4px}
.filter-bottom .gap{display:inline-block;width:18px}

.results{left:166px;top:163px;width:692px;list-style:none}
.result{position:relative;height:32.6px;border-bottom:1px solid var(--rule);font-size:9.5px;color:var(--text-soft)}
.result .title{position:absolute;left:0;top:10px;font-family:"Arimo",sans-serif;font-size:12.5px;color:#333}
.result .state{position:absolute;left:467px;top:10px}
.result .age{position:absolute;left:494px;top:11px}
.result .size{position:absolute;left:553px;top:11px}
.badge{position:absolute;top:9px;width:12px;height:13px;color:#fff;font-size:9px;text-align:center;line-height:13px}
.badge.peers{left:595px;background:var(--badge-blue)}
.badge.seeds{left:651px;background:var(--badge-green)}
.result .peers-n{position:absolute;left:610px;top:11px}
.result .seeds-n{position:absolute;left:665px;top:11px}

.pager{left:0;width:1024px;top:611px;text-align:center;font-size:13.5px;color:#555}
.pager .on{color:var(--accent-green)}
.pager .sep{margin:0 5px}

.social{left:458px;top:684px;display:flex;gap:18px}
.social span{width:24px;height:24px;border-radius:3px;display:block}
.social .feed{background:var(--accent-orange)}
.social .bird{background:#8fc8e6}
.social .book{background:#3a66b0}

.footer{left:6px;top:733px;width:1012px;height:30px;background:linear-gradient(#3a3a3a,var(--bar-dark));color:#fff;font-size:10.5px;text-align:center;padding-top:8px;letter-spacing:.1px}
.footer a{color:var(--accent-green)}
</style>
</head>
<body>
<div class="stage">
  <header class="topbar abs">
    <nav class="nav">
      <a class="current" href="#">HOME</a><span class="sep">|</span><a href="#">ABOUT US</a><span class="sep">|</span><a href="#">TORRENT SEARCH</a><span class="sep">|</span><a href="#">SITE SEARCH</a><span class="sep">|</span><a href="#">HELP</a><span class="sep">|</span><a href="#">LOGIN</a><span class="sep">|</span><a href="#">SIGNIN</a>
    </nav>
    <div class="lang">English<svg width="7" height="6" viewBox="0 0 7 6"><path d="M0 0H7L3.5 6Z" fill="#fff"/></svg></div>
  </header>

  <div class="brand abs">
    <div class="brand-row"><span class="brand-mark"></span><span class="brand-name">Qentrova</span></div>
    <div class="brand-tag">TORRENTS SEARCH ENGINE</div>
  </div>

  <div class="search-field abs">starforgers 3</div>
  <div class="search-btn abs"><svg width="8" height="8" viewBox="0 0 8 8"><circle cx="3.2" cy="3.2" r="2.3" fill="none" stroke="#fff" stroke-width="1.2"/><path d="M5 5L7.5 7.5" stroke="#fff" stroke-width="1.4"/></svg>SEARCH</div>
  <div class="result-stats abs">About 50,000 results (0.12 seconds)</div>
  <div class="site-include abs">Sites search include <i></i></div>

  <div class="filter-top abs">
    <span class="count">1 - 10 of 20 for " starforgers 3 " ( 1,155s )</span>
    <span class="order">Order by : | <span class="red">name</span> | date | size | peers | seeds</span>
  </div>
  <div class="pager-tab abs">previous | 1 | 2 | <span class="on">3</span> | 4 | next</div>
  <div class="filter-bottom abs">Quality : | <span class="red">all</span> | good | bad | verified<span class="gap"></span>Search by : | filename | <span class="red">titles</span> | data added</div>

  <ul class="results abs">
    <li class="result"><span class="title">starforgers 3 &nbsp;HD XVD bgfsbsb.225</span><svg class="state" width="13" height="13" viewBox="0 0 13 13"><circle cx="6.5" cy="6.5" r="5.5" fill="none" stroke="#3aa84a" stroke-width="1.6"/><path d="M6.5 3.5V9.5M3.5 6.5H9.5" stroke="#3aa84a" stroke-width="1.6"/></svg><span class="age">3 days ago</span><span class="size">549 MB</span><span class="badge peers">P</span><span class="peers-n">10.555</span><span class="badge seeds">S</span><span class="seeds-n">10.200</span></li>
    <li class="result"><span class="title">starforgers 3 &nbsp;HD XVD bgfsbsb.225</span><svg class="state" width="13" height="13" viewBox="0 0 13 13"><circle cx="6.5" cy="6.5" r="5.5" fill="none" stroke="#d8201f" stroke-width="1.6"/><path d="M3.5 6.5H9.5" stroke="#d8201f" stroke-width="1.6"/></svg><span class="age">3 days ago</span><span class="size">549 MB</span><span class="badge peers">P</span><span class="peers-n">10.555</span><span class="badge seeds">S</span><span class="seeds-n">10.200</span></li>
    <li class="result"><span class="title">starforgers 3 &nbsp;HD XVD bgfsbsb.225</span><svg class="state" width="13" height="13" viewBox="0 0 13 13"><circle cx="6.5" cy="6.5" r="5.5" fill="none" stroke="#3aa84a" stroke-width="1.6"/><path d="M6.5 3.5V9.5M3.5 6.5H9.5" stroke="#3aa84a" stroke-width="1.6"/></svg><span class="age">3 days ago</span><span class="size">549 MB</span><span class="badge peers">P</span><span class="peers-n">10.555</span><span class="badge seeds">S</span><span class="seeds-n">10.200</span></li>
    <li class="result"><span class="title">starforgers 3 &nbsp;HD XVD bgfsbsb.225</span><svg class="state" width="13" height="13" viewBox="0 0 13 13"><circle cx="6.5" cy="6.5" r="5.5" fill="none" stroke="#3aa84a" stroke-width="1.6"/><path d="M6.5 3.5V9.5M3.5 6.5H9.5" stroke="#3aa84a" stroke-width="1.6"/></svg><span class="age">3 days ago</span><span class="size">549 MB</span><span class="badge peers">P</span><span class="peers-n">10.555</span><span class="badge seeds">S</span><span class="seeds-n">10.200</span></li>
    <li class="result"><span class="title">starforgers 3 &nbsp;HD XVD bgfsbsb.225</span><svg class="state" width="13" height="13" viewBox="0 0 13 13"><circle cx="6.5" cy="6.5" r="5.5" fill="none" stroke="#d8201f" stroke-width="1.6"/><path d="M3.5 6.5H9.5" stroke="#d8201f" stroke-width="1.6"/></svg><span class="age">3 days ago</span><span class="size">549 MB</span><span class="badge peers">P</span><span class="peers-n">10.555</span><span class="badge seeds">S</span><span class="seeds-n">10.200</span></li>
    <li class="result"><span class="title">starforgers 3 &nbsp;HD XVD bgfsbsb.225</span><svg class="state" width="13" height="13" viewBox="0 0 13 13"><circle cx="6.5" cy="6.5" r="5.5" fill="none" stroke="#f08a24" stroke-width="1.6"/><circle cx="6.5" cy="6.5" r="2.6" fill="#f08a24"/></svg><span class="age">3 days ago</span><span class="size">549 MB</span><span class="badge peers">P</span><span class="peers-n">10.555</span><span class="badge seeds">S</span><span class="seeds-n">10.200</span></li>
    <li class="result"><span class="title">starforgers 3 &nbsp;HD XVD bgfsbsb.225</span><svg class="state" width="13" height="13" viewBox="0 0 13 13"><circle cx="6.5" cy="6.5" r="5.5" fill="none" stroke="#3aa84a" stroke-width="1.6"/><path d="M6.5 3.5V9.5M3.5 6.5H9.5" stroke="#3aa84a" stroke-width="1.6"/></svg><span class="age">3 days ago</span><span class="size">549 MB</span><span class="badge peers">P</span><span class="peers-n">10.555</span><span class="badge seeds">S</span><span class="seeds-n">10.200</span></li>
    <li class="result"><span class="title">starforgers 3 &nbsp;HD XVD bgfsbsb.225</span><svg class="state" width="13" height="13" viewBox="0 0 13 13"><circle cx="6.5" cy="6.5" r="5.5" fill="none" stroke="#3aa84a" stroke-width="1.6"/><path d="M6.5 3.5V9.5M3.5 6.5H9.5" stroke="#3aa84a" stroke-width="1.6"/></svg><span class="age">3 days ago</span><span class="size">549 MB</span><span class="badge peers">P</span><span class="peers-n">10.555</span><span class="badge seeds">S</span><span class="seeds-n">10.200</span></li>
    <li class="result"><span class="title">starforgers 3 &nbsp;HD XVD bgfsbsb.225</span><svg class="state" width="13" height="13" viewBox="0 0 13 13"><circle cx="6.5" cy="6.5" r="5.5" fill="none" stroke="#f08a24" stroke-width="1.6"/><circle cx="6.5" cy="6.5" r="2.6" fill="#f08a24"/></svg><span class="age">3 days ago</span><span class="size">549 MB</span><span class="badge peers">P</span><span class="peers-n">10.555</span><span class="badge seeds">S</span><span class="seeds-n">10.200</span></li>
    <li class="result"><span class="title">starforgers 3 &nbsp;HD XVD bgfsbsb.225</span><svg class="state" width="13" height="13" viewBox="0 0 13 13"><circle cx="6.5" cy="6.5" r="5.5" fill="none" stroke="#d8201f" stroke-width="1.6"/><path d="M3.5 6.5H9.5" stroke="#d8201f" stroke-width="1.6"/></svg><span class="age">3 days ago</span><span class="size">549 MB</span><span class="badge peers">P</span><span class="peers-n">10.555</span><span class="badge seeds">S</span><span class="seeds-n">10.200</span></li>
    <li class="result"><span class="title">starforgers 3 &nbsp;HD XVD bgfsbsb.225</span><svg class="state" width="13" height="13" viewBox="0 0 13 13"><circle cx="6.5" cy="6.5" r="5.5" fill="none" stroke="#f08a24" stroke-width="1.6"/><circle cx="6.5" cy="6.5" r="2.6" fill="#f08a24"/></svg><span class="age">3 days ago</span><span class="size">549 MB</span><span class="badge peers">P</span><span class="peers-n">10.555</span><span class="badge seeds">S</span><span class="seeds-n">10.200</span></li>
    <li class="result"><span class="title">starforgers 3 &nbsp;HD XVD bgfsbsb.225</span><svg class="state" width="13" height="13" viewBox="0 0 13 13"><circle cx="6.5" cy="6.5" r="5.5" fill="none" stroke="#3aa84a" stroke-width="1.6"/><path d="M6.5 3.5V9.5M3.5 6.5H9.5" stroke="#3aa84a" stroke-width="1.6"/></svg><span class="age">3 days ago</span><span class="size">549 MB</span><span class="badge peers">P</span><span class="peers-n">10.555</span><span class="badge seeds">S</span><span class="seeds-n">10.200</span></li>
    <li class="result"><span class="title">starforgers 3 &nbsp;HD XVD bgfsbsb.225</span><svg class="state" width="13" height="13" viewBox="0 0 13 13"><circle cx="6.5" cy="6.5" r="5.5" fill="none" stroke="#3aa84a" stroke-width="1.6"/><path d="M6.5 3.5V9.5M3.5 6.5H9.5" stroke="#3aa84a" stroke-width="1.6"/></svg><span class="age">3 days ago</span><span class="size">549 MB</span><span class="badge peers">P</span><span class="peers-n">10.555</span><span class="badge seeds">S</span><span class="seeds-n">10.200</span></li>
  </ul>

  <div class="pager abs">previous<span class="sep">|</span>1<span class="sep">|</span>2<span class="sep">|</span><span class="on">3</span><span class="sep">|</span>4<span class="sep">|</span>next</div>

  <div class="social abs" aria-label="Social links">
    <span class="feed"></span><span class="bird"></span><span class="book"></span>
  </div>

  <footer class="footer abs">COPYRIGHT © 2011 QENTROVA. USE OF THIS WEBSITE CONSTITUTES ACCEPTANCE OF OUR <a href="#">USER AGREEMENT</a> AND <a href="#">PRIVACY POLICY</a>.</footer>
</div>
</body>
</html>
```